Small Catering Menu

I am looking to make a small menu for catering for my company. I am thinking of a small A5 size booklet which will also have some pictures and the cover needs to be attractive.
Likely to be 8-12 pages depending upon your design (could be less or more). I need 2-3 pages as proposal concept (Cover, inside first page and one menu page) and if we like it we will make the project guaranteed before finishing the rest of the project to add security for the designer.
Pictures will be provided to the designer whose concept is the best as they are too heavy. But use generic photos for now (rather large ones) if possible.
Logo is available and so is the inside text as well as some other tidbits.
I will provide the fonts too to ensure it maintains the corporate integrity that we are following.
Industry/Entity Type
Catering

```html
<!DOCTYPE html>
<html lang="en">
<head>
<meta charset="utf-8">
<title>By the sea – Catering Menu</title>
<link href="https://fonts.googleapis.com/css2?family=Source+Sans+3:wght@300;400;600&family=Tinos&display=swap" rel="stylesheet">
<style>
:root{
  --paper:#f4f4f4;
  --ink:#2b2b2b;
  --muted:#444;
  --red:#e3151b;
  --dark:#231f20;
  --white:#ffffff;
  --rule:#e2e2e2;
  --frame:#d0d0d0;
  --grey-text:#6e6e6e;
}
*{margin:0;padding:0;box-sizing:border-box}
html,body{width:1200px;height:783px;overflow:hidden}
body{background:var(--paper);font-family:"Source Sans 3",Arial,sans-serif;color:var(--ink);position:relative}
.abs{position:absolute}
.menu-title{left:46px;top:30px;font-size:56px;font-weight:300;letter-spacing:1px;color:#333;line-height:1}
.menu-intro{left:318px;top:50px;font-size:14.5px;line-height:22px;color:#222}
.section-head{color:var(--red);font-size:22px;font-weight:400;text-align:center;line-height:1}
.head-rule{height:1px;background:var(--rule)}
.item-no{font-size:30px;font-weight:300;color:#333;line-height:1}
.item-name{font-size:13px;color:#222;line-height:16px}
.item-desc{font-size:9px;color:#222;line-height:11px}
.item-dots{border-bottom:1px dotted #555;height:1px}
.price{color:var(--red);font-size:11px}
.desserts-box{left:903px;top:63px;width:251px;height:147px;border:1px solid var(--frame);background:var(--white)}
.desserts-title{left:912px;top:47px;background:var(--paper);padding:0 10px;color:var(--red);font-size:22px}
.dessert-photo{width:90px;height:38px;background:linear-gradient(90deg,#3b1c0f,#8a4a22 50%,#2d140a)}
.courses-panel{left:0;top:480px;width:632px;height:303px;background:var(--dark)}
.courses-title{left:0;top:497px;width:632px;text-align:center;font-family:"Tinos",serif;color:var(--white);font-size:24px}
.courses-rule{height:1px;background:#bdbdbd;top:511px}
.course-photo{top:550px;height:101px}
.course-card{top:663px;width:190px;text-align:center}
.course-name{color:var(--white);font-size:12.5px;line-height:16px}
.course-desc{color:var(--grey-text);font-size:9px;margin-top:1px}
.course-price{color:var(--red);font-size:12.5px;margin-top:3px}
.drinks-box{left:639px;top:480px;width:516px;height:274px;border:1px solid var(--frame);background:var(--white)}
.drinks-title{left:845px;top:460px;width:104px;height:34px;background:var(--white);color:var(--red);font-size:22px;text-align:center;line-height:34px}
.drink-photo{top:500px;width:119px;height:177px;background:radial-gradient(circle at 60% 30%,#7b9a86,#2f4d3c 55%,#1c2e24);overflow:hidden}
.drink-badge{position:absolute;left:50%;bottom:-60px;width:120px;height:120px;margin-left:-60px;border-radius:50%;background:var(--white);text-align:center;padding-top:20px;color:var(--red);font-size:11px}
.drink-name{top:690px;width:125px;text-align:center;font-size:11.5px;line-height:12px;color:#222}
.drinks-note{left:647px;top:734px;font-size:10.5px;color:#222}
</style>
</head>
<body>

<h1 class="abs menu-title">By the sea</h1>
<p class="abs menu-intro">Choose one item from each category<br>Pricing is OMR 4 per person</p>

<!-- Appetizer -->
<div class="abs head-rule" style="left:40px;top:136px;width:535px"></div>
<h2 class="abs section-head" style="left:240px;top:123px;width:120px;background:var(--paper)">Appetizer</h2>

<div class="abs item-no" style="left:48px;top:161px">01</div>
<div class="abs item-name" style="left:88px;top:160px">Dynamite Shrimps</div>
<div class="abs item-desc" style="left:86px;top:176px">your food item description, ingredients etc..</div>
<div class="abs item-dots" style="left:355px;top:184px;width:128px"></div>
<div class="abs price" style="left:523px;top:180px">$4,5</div>

<div class="abs item-no" style="left:48px;top:217px">02</div>
<div class="abs item-name" style="left:93px;top:216px">Tuna Fish Cutlets.</div>
<div class="abs item-desc" style="left:94px;top:232px">your food item description, ingredients etc.. goes here</div>
<div class="abs item-dots" style="left:355px;top:240px;width:128px"></div>
<div class="abs price" style="left:523px;top:235px">$4,5</div>

<!-- Sandwiches -->
<div class="abs head-rule" style="left:40px;top:296px;width:535px"></div>
<h2 class="abs section-head" style="left:230px;top:284px;width:140px;background:var(--paper)">Sandwiches</h2>

<div class="abs item-no" style="left:48px;top:323px">04</div>
<div class="abs item-name" style="left:87px;top:322px">Tuna Sanwich</div>
<div class="abs item-desc" style="left:86px;top:338px">your food item description, ingredients etc.. goes here</div>
<div class="abs item-dots" style="left:355px;top:346px;width:128px"></div>
<div class="abs price" style="left:523px;top:341px">$8.50</div>

<div class="abs item-no" style="left:48px;top:383px">05</div>
<div class="abs item-name" style="left:87px;top:383px">Pan Fried Baja Fish Fillet in<br>Ciabatta Bread whith Cheese</div>
<div class="abs item-desc" style="left:86px;top:416px">your food item description...</div>
<div class="abs item-dots" style="left:355px;top:420px;width:128px"></div>
<div class="abs price" style="left:523px;top:414px">$6.99</div>

<!-- Salads -->
<h2 class="abs section-head" style="left:648px;top:58px;text-align:left">Salads</h2>
<div class="abs head-rule" style="left:649px;top:85px;width:104px;background:#d6d6d6"></div>

<div class="abs item-no" style="left:650px;top:113px;font-size:24px">01</div>
<div class="abs item-name" style="left:685px;top:111px;font-size:11px;line-height:13px">Dynamite Shrimps</div>
<div class="abs item-desc" style="left:685px;top:123px;font-size:7.5px">your food item description, ingredients etc..</div>
<div class="abs item-dots" style="left:842px;top:127px;width:12px"></div>
<div class="abs price" style="left:862px;top:121px">$4,5</div>

<div class="abs item-no" style="left:650px;top:170px;font-size:24px">02</div>
<div class="abs item-name" style="left:683px;top:172px;font-size:11px;line-height:13px">Tuna Fish Cutlets.</div>
<div class="abs item-desc" style="left:684px;top:183px;font-size:7.5px">your food item description, ingredients etc..</div>
<div class="abs item-dots" style="left:842px;top:188px;width:12px"></div>
<div class="abs price" style="left:862px;top:180px">$4,5</div>

<!-- Desserts -->
<div class="abs desserts-box"></div>
<h2 class="abs desserts-title">Desserts</h2>
<div class="abs dessert-photo" role="img" aria-label="Coffee cups with beans and a leaf" style="left:911px;top:87px"></div>
<div class="abs item-name" style="left:1010px;top:81px">Tuna Sanwich</div>
<div class="abs price" style="left:1112px;top:84px">$4,5</div>
<div class="abs item-desc" style="left:1010px;top:99px;font-size:9.5px;line-height:12px">your food item description,<br>ingredients etc.. goes here</div>

<div class="abs dessert-photo" role="img" aria-label="Coffee cups with beans and a leaf" style="left:911px;top:152px"></div>
<div class="abs item-name" style="left:1010px;top:148px">Tuna Sanwich</div>
<div class="abs price" style="left:1112px;top:151px">$4,5</div>
<div class="abs item-desc" style="left:1010px;top:166px;font-size:9.5px;line-height:12px">your food item description,<br>ingredients etc.. goes here</div>

<!-- Soups -->
<div class="abs head-rule" style="left:649px;top:268px;width:505px"></div>
<h2 class="abs section-head" style="left:855px;top:255px;width:90px;background:var(--paper)">Soups</h2>

<div class="abs item-no" style="left:648px;top:302px">01</div>
<div class="abs item-name" style="left:689px;top:305px">Dynamite Shrimps</div>
<div class="abs item-desc" style="left:688px;top:321px">your food item description, ingredients etc..</div>
<div class="abs item-dots" style="left:956px;top:329px;width:127px"></div>
<div class="abs price" style="left:1124px;top:325px">$4,5</div>

<div class="abs item-no" style="left:648px;top:373px">02</div>
<div class="abs item-name" style="left:693px;top:374px">Tuna Fish Cutlets.</div>
<div class="abs item-desc" style="left:694px;top:390px">your food item description, ingredients etc.. goes here</div>
<div class="abs item-dots" style="left:956px;top:397px;width:127px"></div>
<div class="abs price" style="left:1124px;top:392px">$4,5</div>

<!-- Main Courses -->
<div class="abs courses-panel"></div>
<div class="abs courses-rule" style="left:53px;width:178px"></div>
<div class="abs courses-rule" style="left:402px;width:184px"></div>
<h2 class="abs courses-title">Main Courses</h2>

<div class="abs course-photo" role="img" aria-label="Cheese wedges with cherry tomatoes" style="left:45px;width:164px;background:linear-gradient(135deg,#2a1a10,#c9b07a 55%,#5a2a14)"></div>
<div class="abs course-photo" role="img" aria-label="Spiky orange horned melon halves" style="left:229px;width:165px;background:radial-gradient(circle at 55% 55%,#d9651d,#7a3614 55%,#2a1609)"></div>
<div class="abs course-photo" role="img" aria-label="Golden croissants" style="left:412px;width:168px;background:radial-gradient(ellipse at 50% 55%,#e09a3c,#f3d29a 50%,#ffffff 72%)"></div>

<div class="abs course-card" style="left:32px">
  <div class="course-name">Pan Fried Baja Fish Fillet in<br>Ciabatta Bread whith Cheese</div>
  <div class="course-desc">your food item description...</div>
  <div class="course-price">$6.99</div>
</div>
<div class="abs course-card" style="left:216px">
  <div class="course-name">Pan Fried Baja Fish Fillet in<br>Ciabatta Bread whith Cheese</div>
  <div class="course-desc">your food item description...</div>
  <div class="course-price">$6.99</div>
</div>
<div class="abs course-card" style="left:400px">
  <div class="course-name">Pan Fried Baja Fish Fillet in<br>Ciabatta Bread whith Cheese</div>
  <div class="course-desc">your food item description...</div>
  <div class="course-price">$6.99</div>
</div>

<!-- Drinks -->
<div class="abs drinks-box"></div>
<h2 class="abs drinks-title">Drinks</h2>

<div class="abs drink-photo" role="img" aria-label="Kiwi juice glass with straw" style="left:649px"><span class="drink-badge">$4,5</span></div>
<div class="abs drink-photo" role="img" aria-label="Kiwi juice glass with straw" style="left:775px"><span class="drink-badge">$4,5</span></div>
<div class="abs drink-photo" role="img" aria-label="Kiwi juice glass with straw" style="left:901px"><span class="drink-badge">$4,5</span></div>
<div class="abs drink-photo" role="img" aria-label="Kiwi juice glass with straw" style="left:1026px"><span class="drink-badge">$4,5</span></div>

<div class="abs drink-name" style="left:645px">Choice of Fresh Juices</div>
<div class="abs drink-name" style="left:771px;width:130px">Soda “Crestline Cola”<br>or<br>Water</div>
<div class="abs drink-name" style="left:897px">Lemon Mint</div>
<div class="abs drink-name" style="left:1022px">Iced Tea</div>

<p class="abs drinks-note">An Additional 10% for replacement of everi &nbsp;item on the menu with another from outside the menu (per head)</p>

</body>
</html>
```